Corvane Business Cards

Front of business card will have logo, name, address, & telephone number. Back of card will have a list of services provided - Roads, Substation Pads, Temporary Pads, Site Pads, Land Leveling, Powerline Row Cleaning, Land Clearing, Gates, Fencing, Construction Entrances, Excavation, Trenching, Underground Utilities, Directional Boring, Pile Driving. We are a construction company that uses heavy equipment like bulldozers, motor graders/blades, dump trucks, backhoes, hydro axes, & skid loaders. We build roads, pads, & install electric utility lines & waterlines underground. This logo is new. The word "Construction" can be smaller as uploaded 2 example edited logos. We will be using this card design for many employees.
Target Market(s)
Industrial Electric Powerline, Wind Turbine, Solar Panel, & Water Utility companies.
Contact Information for Business Card
Name/Position - Dwayne Halster - Owner
Address: 4875 FM 309
Caddo Flats, NM 88241
Phone number - (575) 482-5096

```html
<!DOCTYPE html>
<html lang="en">
<head>
<meta charset="utf-8">
<title>Corvane Construction – Business Card</title>
<link href="https://fonts.googleapis.com/css2?family=Arimo:wght@400;700&family=Marcellus&display=swap" rel="stylesheet">
<style>
  :root{
    --stage:#3b3431;
    --paper:#f7f7f5;
    --maroon:#4a1420;
    --maroon-deep:#3c0f19;
    --ink:#4a1420;
    --grey:#6e6e6e;
    --phone:#333333;
    --rule:#9a9a9a;
    --back-text:#f3ecec;
    --back-rule:rgba(255,255,255,.28);
  }
  *{box-sizing:border-box;margin:0;padding:0}
  html,body{width:1200px;height:844px;overflow:hidden}
  body{
    background:var(--stage);
    font-family:"Arimo",Arial,sans-serif;
    display:flex;align-items:center;justify-content:center;gap:48px;
  }
  .card{
    width:540px;height:309px;border-radius:3px;flex:none;
    box-shadow:0 10px 30px rgba(0,0,0,.35);
    position:relative;overflow:hidden;
  }
  /* Front */
  .card-front{background:var(--paper);display:flex;align-items:center}
  .brand{
    width:270px;flex:none;display:flex;flex-direction:column;align-items:center;justify-content:center;gap:12px;
  }
  .brand-mark{width:22px;height:22px;background:var(--maroon)}
  .brand-name{
    font-family:"Marcellus",serif;color:var(--maroon);
    font-size:34px;letter-spacing:2px;text-transform:uppercase;line-height:1;text-align:center;
  }
  .brand-sub{
    font-family:"Marcellus",serif;color:var(--maroon);
    font-size:22px;letter-spacing:1px;text-transform:uppercase;line-height:1;
  }
  .divider{width:1px;height:150px;background:var(--rule);flex:none}
  .contact{padding-left:24px;padding-right:16px;min-width:0}
  .contact-name{font-weight:700;font-size:20px;color:var(--ink);letter-spacing:.3px;line-height:1;white-space:nowrap}
  .contact-role{font-size:14px;color:var(--grey);margin-top:4px}
  .contact-phone{font-weight:700;font-size:17px;color:var(--phone);margin-top:18px;white-space:nowrap}
  .contact-phone span{color:var(--ink)}
  .contact-address{font-size:15px;color:var(--grey);margin-top:14px;line-height:1.35;white-space:nowrap}
  /* Back */
  .card-back{
    background:var(--maroon-deep);color:var(--back-text);
    display:flex;flex-direction:column;align-items:center;justify-content:center;
    text-align:center;padding:0 24px;
  }
  .back-block{font-size:13.5px;line-height:1.5}
  .back-rule{width:150px;height:1px;background:var(--back-rule);margin:12px 0}
</style>
</head>
<body>
  <section class="card card-front" aria-label="Business card front">
    <div class="brand">
      <div class="brand-mark"></div>
      <div class="brand-name">Corvane</div>
      <div class="brand-sub">Construction</div>
    </div>
    <div class="divider"></div>
    <div class="contact">
      <div class="contact-name">DWAYNE HALSTER</div>
      <div class="contact-role">Owner</div>
      <div class="contact-phone"><span>P:</span> (575) 482-5096</div>
      <div class="contact-address">4875 FM 309<br>Caddo Flats, NM 88241</div>
    </div>
  </section>

  <section class="card card-back" aria-label="Business card back">
    <p class="back-block">
      Roads | Substation Pads | Temporary Pads | Site Pads,<br>
      Land Leveling | Powerline Row Cleaning | Land Clearing<br>
      Gates | Fencing, Construction Entrances | Excavation<br>
      Trenching | Underground Utilities | Directional Boring | Pile Driving.
    </p>
    <div class="back-rule"></div>
    <p class="back-block">
      We are a construction company that uses heavy equipment<br>
      like bulldozers | motor graders/blades | dump trucks<br>
      backhoes | hydro axes &amp; skid loaders.
    </p>
    <div class="back-rule"></div>
    <p class="back-block">
      We build roads, pads<br>
      install electric utility lines &amp; waterlines underground.
    </p>
  </section>
</body>
</html>
```